I work in creative/artistic projects across different mediums.
It needs to communicate creativity, style, sexy, uniqueness, individuality and sophistication.
It should not look corporate.
Colours I like are black silver gold deep purple, chocolate, orchid.
It doesn't have to make use of all these colours.
I do not like bright primary colors.
Updates

Project Deadline Extended
Reason: Still in the communication process and to allow the person enough time to finish the design. Though i should know in the next day or two. Thank you.

Target Market(s)

creatives and companies wanting to inject creativity into thier business.

Industry/Entity Type

Work

Contact Information for Business Card

Corwin Haldley
0418592036
corwin@corwinhaldley-example.com

quietgoldenhourstudio.example.au

Requirements
Should not have
• Anything corporate OR OLD FASHIONED

```html
<!DOCTYPE html>
<html lang="en">
<head>
<meta charset="utf-8">
<title>Corwin Haldley — Business Card</title>
<link rel="stylesheet" href="https://fonts.googleapis.com/css2?family=Italianno&family=Tenor+Sans&family=Open+Sans:wght@400&display=swap">
<style>
  :root {
    --backdrop: #8a8a8a;
    --card-black: #030303;
    --gold-light: #e9d3a6;
    --gold-mid: #b8955f;
    --gold-deep: #6e5230;
    --ink-white: #f4f4f4;
  }
  * { box-sizing: border-box; margin: 0; padding: 0; }
  html, body {
    width: 1200px;
    height: 1200px;
    overflow: hidden;
  }
  body {
    background: var(--backdrop);
    display: flex;
    flex-direction: column;
    align-items: center;
    justify-content: center;
    gap: 56px;
  }
  .card {
    position: relative;
    width: 840px;
    height: 514px;
    background: var(--card-black);
    box-shadow: 0 18px 40px rgba(0,0,0,0.35);
  }

  /* Front */
  .card-front .signature-name {
    position: absolute;
    left: 0;
    right: 0;
    top: 50%;
    transform: translateY(-50%);
    text-align: center;
    font-family: "Italianno", cursive;
    font-size: 104px;
    letter-spacing: 4px;
    line-height: 1;
    background: linear-gradient(100deg, var(--gold-deep) 0%, var(--gold-light) 35%, var(--gold-mid) 60%, var(--gold-light) 85%, var(--gold-mid) 100%);
    -webkit-background-clip: text;
    background-clip: text;
    color: transparent;
  }

  /* Back */
  .contact-list {
    position: absolute;
    left: 62px;
    top: 200px;
    list-style: none;
    font-family: "Open Sans", sans-serif;
    font-size: 17px;
    line-height: 34px;
    color: var(--ink-white);
  }
  .gold-divider {
    position: absolute;
    left: 418px;
    top: 150px;
    width: 3px;
    height: 214px;
  }
  .card-back .display-name {
    position: absolute;
    left: 470px;
    top: 50%;
    transform: translateY(-50%);
    font-family: "Tenor Sans", sans-serif;
    font-size: 26px;
    letter-spacing: 5px;
    text-transform: uppercase;
    color: var(--ink-white);
    white-space: nowrap;
  }
</style>
</head>
<body>
  <section class="card card-front">
    <h1 class="signature-name">Corwin Haldley</h1>
  </section>

  <section class="card card-back">
    <ul class="contact-list">
      <li>M: 0418592036</li>
      <li>E: corwin@corwinhaldley-example.com</li>
      <li>W: quietgoldenhourstudio.example.au</li>
    </ul>
    <svg class="gold-divider" viewBox="0 0 3 214" preserveAspectRatio="none" aria-hidden="true">
      <defs>
        <linearGradient id="divider-gold" x1="0" y1="0" x2="0" y2="1">
          <stop offset="0" stop-color="var(--gold-deep)"/>
          <stop offset="0.35" stop-color="var(--gold-light)"/>
          <stop offset="0.7" stop-color="var(--gold-mid)"/>
          <stop offset="1" stop-color="var(--gold-deep)"/>
        </linearGradient>
      </defs>
      <rect width="3" height="214" fill="url(#divider-gold)"/>
    </svg>
    <p class="display-name">Corwin Haldley</p>
  </section>
</body>
</html>
```